Research and Innovation programme/projects in WOOD based industries

1.Pramenova s.r.o. (offical registered brand name of our company)
-Managing technology development projects
-International cooperation and development European projects
Our company was founded in 2008 and started to work as a counsilary company operating in the section of european funds administrated by Czech republic. Nowadays we are specializing on projects in the sphere of science and research co-financed by EU.Since 6.6.2013 we are registered under European comission for a purpose of broad support of transnational projects.

Target Market(s)

We are primarily focused on european companies, which stand behind the latest research and innovation of sawing, planing, glulam and logging technologies based on wooden materials.

Coding

Coded - Design and coding required

Number of Pages Required

5+ page

Font styles to use
Serif

Colors
cadf82
abd037
9bcb3c
fee18a
ffcf3e
ffc214

Requirements
Must have
• The web will exist in three possible languages in czech, english and deutsch.
• First page : introduction of a company
• Second page : Area of expertise
• Third page: servicies our company provides
• Fourth page: Our partners
• Fifth page: Conditions of our servicies
• Sixth page: Succesful projects
• - we would also love if we had possibility to add videos about our successful projects
• Seventh: Our team
• We are serious company in the sphere of funds and counsilary servicies, that is why we would love to have web design as representative as possible
• Take on mind that that we are specializing on development management, try to apply that on your design
• In the section of contacts, we would love to have photos of our team,
• This is our current site: http://www.pramenova-example.eu/cz/partneri.html
• This is how our concurency sites are lookin. Take these designs as an slight inspiration.
• http://www.lumatrava-example.sk/en/
• https://www2.brenvick-example.com/global/en.html
Nice to have
• Visible logo on the front page for the visitor.
• As a inspiration we provided link for our current web design, but we dont want to copy the current style, just look at the logo and the pages that exists on current web.
• !!!!!!We also uploaded file, where we explain how our cooperation with partner works. Especially in the part 2. section of service. Take that as an ispiration too, or use that to understand, what our company do.
Should not have
• We are serious company in the sphere of funds and counsilary servicies, that is why we would love to have web design representative as possible

```html
<!DOCTYPE html>
<html lang="en">
<head>
<meta charset="utf-8">
<title>Pramenova – Research and Innovation programme</title>
<link href="https://fonts.googleapis.com/css2?family=Raleway:wght@500;600;700;800&family=Open+Sans:wght@400;600&display=swap" rel="stylesheet">
<style>
:root{
  --green:#9bcb3c;
  --green-dark:#8cc63f;
  --green-light:#cadf82;
  --lime:#abd037;
  --yellow:#ffc214;
  --yellow-mid:#ffcf3e;
  --yellow-light:#fee18a;
  --text:#4a4a4a;
  --muted:#666;
  --grey-bg:#f4f4f4;
  --team-bg:#f8f4f3;
  --white:#fff;
}
*{box-sizing:border-box;margin:0;padding:0}
html,body{width:1200px;height:5190px;overflow:hidden}
body{font-family:"Open Sans",sans-serif;color:var(--text);background:var(--white);font-size:13px;line-height:1.9}
h1,h2,h3,h4,.label,.brand{font-family:"Raleway",sans-serif}
section,header,footer{position:relative;width:1200px;overflow:hidden}
.abs{position:absolute}
.label{display:inline-block;font-size:13px;font-weight:700;color:var(--white);padding:8px 22px;text-transform:uppercase;letter-spacing:.2px}
.label.green{background:var(--green)}
.label.yellow{background:var(--yellow)}
.label.white{background:var(--white);color:var(--yellow)}
.center{left:0;right:0;text-align:center}
.sec-title{font-size:25px;font-weight:800;text-transform:uppercase;letter-spacing:.3px}

/* header */
.site-header{height:97px;background:var(--green)}
.brand{display:flex;align-items:center;gap:10px;color:var(--white);font-weight:700;font-size:22px}
.brand .mark{width:34px;height:26px;background:var(--yellow)}
.site-header .brand{position:absolute;left:110px;top:33px}
.nav{position:absolute;left:300px;top:39px;display:flex;gap:26px;font-family:"Raleway",sans-serif;font-size:11.5px;font-weight:600;color:var(--white)}
.lang{position:absolute;left:1036px;top:40px;display:flex;align-items:center;gap:6px}

/* hero */
.hero{height:573px}
.hero-photo{position:absolute;inset:0;background:linear-gradient(180deg,#8ea3ae 0%,#7a8a8c 30%,#5e6a5a 60%,#3f4a3a 100%)}
.hero-title{position:absolute;left:430px;top:161px;width:340px;height:88px;background:var(--yellow);color:var(--white);font-family:"Raleway",sans-serif;font-weight:700;font-size:46px;text-align:center;line-height:88px}
.hero-sub{position:absolute;left:406px;top:289px;width:390px;height:49px;background:var(--green);color:var(--white);font-family:"Raleway",sans-serif;font-weight:700;font-size:14px;text-align:center;line-height:49px}

/* about */
.about{height:518px}
.about .label{position:absolute;left:110px;top:119px}
.about h2{position:absolute;left:110px;top:192px;color:var(--green-dark)}
.about p{position:absolute;left:110px;top:246px;width:466px;font-size:12.5px;line-height:25px}
.about-photo{position:absolute;left:646px;top:65px;width:441px;height:364px;border:3px solid var(--green-light);background:linear-gradient(180deg,#c9ccd0 0%,#a7abae 45%,#bdb6ad 60%,#8d8680 100%)}

/* expertise */
.expertise{height:453px;background:linear-gradient(135deg,var(--yellow) 0%,var(--yellow-mid) 50%,var(--yellow) 100%)}
.expertise .label{position:absolute;left:514px;top:86px}
.expertise h2{position:absolute;top:145px;color:var(--white);line-height:31px}
.expertise p{position:absolute;left:215px;width:770px;top:238px;color:var(--white);text-align:center;font-size:12.5px;line-height:25px}

/* services */
.services{height:920px;background:var(--grey-bg)}
.services .label{position:absolute;left:447px;top:80px}
.services h2{position:absolute;top:148px;color:var(--green-dark)}
.svc{position:absolute;width:330px}
.svc .ico{position:absolute;left:-128px;top:-20px;width:100px;height:100px;border-radius:50%;border:1px solid #ddd;background:var(--grey-bg);display:flex;align-items:center;justify-content:center}
.svc h4{font-size:13.5px;font-weight:700;color:#333;line-height:17px;margin-bottom:8px}
.svc p{font-size:11.5px;line-height:24px;color:var(--muted)}
.vline{position:absolute;width:1px;background:#ddd}

/* partners */
.partners{height:368px;background:var(--green)}
.partners .label{position:absolute;left:525px;top:82px}
.partners .lead{position:absolute;top:128px;color:var(--white);font-size:12.5px}
.logos{position:absolute;left:140px;top:220px;width:920px;display:flex;justify-content:space-between;align-items:center}
.logo-name{display:flex;align-items:center;gap:8px;color:var(--white);font-family:"Raleway",sans-serif;font-weight:700;font-size:22px}
.logo-name .dot{width:26px;height:26px;border-radius:50%;background:var(--white)}
.arrow{position:absolute}

/* conditions */
.conditions{height:544px}
.cond-photo{position:absolute;left:113px;top:82px;width:439px;height:362px;border:3px solid var(--yellow-mid);background:linear-gradient(180deg,#5d5a52 0%,#8f7f64 45%,#c8b89c 70%,#a9a49a 100%)}
.conditions .label{position:absolute;left:610px;top:125px}
.conditions h2{position:absolute;left:610px;top:188px;color:var(--yellow)}
.conditions p{position:absolute;left:610px;top:236px;width:470px;font-size:12.5px;line-height:25px}

/* projects */
.projects{height:724px;background:linear-gradient(120deg,var(--green-light) 0%,#b5cf6e 40%,#a8a84e 75%,#b49a48 100%)}
.projects .label{position:absolute;left:500px;top:92px}
.projects h2{position:absolute;top:146px;color:var(--white)}
.card{position:absolute;top:239px;width:311px;height:388px;background:var(--white)}
.card .media{height:207px;position:relative}
.card .play{position:absolute;left:125px;top:73px;width:62px;height:62px;border-radius:50%;background:rgba(255,255,255,.8);display:flex;align-items:center;justify-content:center}
.card h3{font-size:19px;font-weight:600;color:#333;text-align:center;margin-top:30px}
.card p{font-size:11.5px;line-height:23px;text-align:center;padding:0 30px;margin-top:10px;color:var(--muted)}

/* team */
.team{height:584px;background:var(--team-bg)}
.team .label{position:absolute;left:545px;top:87px}
.team .lead{position:absolute;top:140px;font-size:13px}
.member{position:absolute;top:200px;width:520px;text-align:center}
.member .photo{width:212px;height:212px;margin:0 auto;border-radius:50%;background:var(--white);padding:12px;box-shadow:0 0 0 1px #e8e2e0}
.member .photo div{width:100%;height:100%;border-radius:50%}
.member h3{font-size:23px;font-weight:500;color:#222;margin-top:10px;line-height:28px}
.member .role{font-size:14px;color:#333;line-height:20px}
.member .contacts{font-size:10.5px;color:var(--muted);margin-top:12px;display:flex;justify-content:center;gap:18px}

/* footer */
.site-footer{height:409px;background:var(--green);color:var(--white)}
.site-footer .brand{position:absolute;left:110px;top:82px}
.f-about{position:absolute;left:110px;top:130px;width:310px;font-size:10px;line-height:25px}
.social{position:absolute;left:112px;top:255px;display:flex;gap:10px}
.social span{width:10px;height:10px;background:var(--white);border-radius:2px}
.site-footer h4{position:absolute;font-size:15px;font-weight:700}
.links{position:absolute;font-size:11px;line-height:33px}
.newsletter input{position:absolute;left:850px;top:120px;width:240px;height:42px;border:none;padding:0 20px;font-size:11px;font-family:"Open Sans",sans-serif}
.subscribe{position:absolute;left:995px;top:178px;width:95px;height:40px;background:var(--yellow);font-size:11px;font-weight:600;text-align:center;line-height:40px}
.copy{position:absolute;top:352px;font-size:11px}
</style>
</head>
<body>

<header class="site-header">
  <div class="brand"><span class="mark"></span>Pramenova</div>
  <nav class="nav">
    <span>About</span><span>Area of Expertise</span><span>Services</span><span>Our Partners</span><span>Conditions of Our Services</span><span>Successful Projects</span><span>Our Team</span>
  </nav>
  <div class="lang">
    <svg width="32" height="20" viewBox="0 0 32 20"><rect width="32" height="20" fill="#fff"/><rect x="13" width="6" height="20" fill="#d22"/><rect y="7" width="32" height="6" fill="#d22"/></svg>
    <svg width="10" height="6" viewBox="0 0 10 6"><path d="M0 0h10L5 6z" fill="#fff"/></svg>
  </div>
</header>

<section class="hero">
  <div class="hero-photo" role="img" aria-label="City skyline with a red lattice tower and dense high-rise buildings"></div>
  <div class="hero-title">Pramenova</div>
  <div class="hero-sub">We provide Research and Innovation programme</div>
</section>

<section class="about">
  <span class="label green">About us</span>
  <h2 class="sec-title">Finibus Bonorum et Malorum</h2>
  <p>Our company was founded in 2008 and started to work as a counsilary company operating in the section of European funds administrated by Czech republic. Nowadays we are specialising on projects in the sphere of science and research co-financed by EU.Since 6.6.2013 we are registered under European commission for a purpose of broad support of transna-tional projects.</p>
  <div class="about-photo" role="img" aria-label="Young green seedling growing from cracked dry earth in front of a distant city skyline"></div>
</section>

<section class="expertise">
  <span class="label white">Area of expertise</span>
  <h2 class="sec-title center">Excepteur sint occaecat cupidatat non proident,<br>sunt in culpa qui officia deserunt</h2>
  <p>Lorem ipsum dolor sit amet, consectetur adipiscing elit, sed do eiusmod tempor incididunt ut labore et dolore magna aliqua. Ut enim ad minim veniam, quis nostrud exercitation ullamco laboris nisi ut aliquip ex ea commodo consequat. Duis aute irure dolor in reprehenderit in voluptate velit esse cillum dolore eu fugiat nulla pariatur. Excepteur sint occaecat cupidatat non proident, sunt in culpa qui officia deserunt mollit anim id est laborum.</p>
</section>

<section class="services">
  <span class="label green">Services our company provides</span>
  <h2 class="sec-title center">Quis nostrud exercitation ullamco laboris nisi</h2>

  <div class="vline" style="left:163px;top:281px;height:600px"></div>
  <div class="vline" style="left:704px;top:350px;height:320px"></div>

  <div class="svc" style="left:241px;top:281px"><div class="ico"><svg width="40" height="40" viewBox="0 0 40 40" fill="none" stroke="#9bcb3c" stroke-width="1.5"><circle cx="20" cy="11" r="5"/><rect x="8" y="20" width="24" height="14"/><path d="M8 26h24"/></svg></div><h4>Project Coordination</h4><p>Sed do eiusmod tempor incididunt ut labore et dolore magna aliqua</p></div>
  <div class="svc" style="left:241px;top:436px"><div class="ico"><svg width="40" height="40" viewBox="0 0 40 40" fill="none" stroke="#9bcb3c" stroke-width="1.5"><circle cx="11" cy="13" r="6"/><path d="M18 34V26M24 34V20M30 34V14M36 34V8M4 34h34"/></svg></div><h4>Project Financing</h4><p>Sed do eiusmod tempor incididunt ut labore et dolore magna aliqua</p></div>
  <div class="svc" style="left:241px;top:591px"><div class="ico"><svg width="40" height="40" viewBox="0 0 40 40" fill="none" stroke="#9bcb3c" stroke-width="1.5"><rect x="6" y="8" width="28" height="18"/><path d="M10 22l7-7 5 4 8-8M14 26l-4 8M26 26l4 8"/></svg></div><h4>Technology and Foreign Trade Projects</h4><p>Sed do eiusmod tempor incididunt ut labore et dolore magna aliqua</p></div>
  <div class="svc" style="left:241px;top:746px"><div class="ico"><svg width="40" height="40" viewBox="0 0 40 40" fill="none" stroke="#9bcb3c" stroke-width="1.5"><circle cx="20" cy="10" r="5"/><rect x="10" y="18" width="20" height="16"/><path d="M10 24h20M10 29h20"/></svg></div><h4>Projects in the Framework of International Cooperation</h4><p>Sed do eiusmod tempor incididunt ut labore et dolore magna aliqua</p></div>

  <div class="svc" style="left:783px;top:350px"><div class="ico"><svg width="40" height="40" viewBox="0 0 40 40" fill="none" stroke="#9bcb3c" stroke-width="1.5"><circle cx="12" cy="12" r="4"/><circle cx="28" cy="12" r="4"/><circle cx="20" cy="22" r="4"/><path d="M5 34c0-6 4-9 7-9M35 34c0-6-4-9-7-9M13 36c0-5 3-8 7-8s7 3 7 8"/></svg></div><h4>EU Projects</h4><p>Sed do eiusmod tempor incididunt ut labore et dolore magna aliqua</p></div>
  <div class="svc" style="left:783px;top:505px"><div class="ico"><svg width="40" height="40" viewBox="0 0 40 40" fill="none" stroke="#9bcb3c" stroke-width="1.5"><rect x="6" y="8" width="28" height="20"/><path d="M10 14h8M10 19h12M14 28v6M26 28v6M8 34h24"/></svg></div><h4>International Development Projects</h4><p>Sed do eiusmod tempor incididunt ut labore et dolore magna aliqua</p></div>
  <div class="svc" style="left:783px;top:658px"><div class="ico"><svg width="40" height="40" viewBox="0 0 40 40" fill="none" stroke="#9bcb3c" stroke-width="1.5"><circle cx="20" cy="18" r="12"/><path d="M8 18h24M20 6c-5 6-5 18 0 24M20 6c5 6 5 18 0 24M14 36h12M20 30v6"/></svg></div><h4>Export Promotion</h4><p>Sed do eiusmod tempor incididunt ut labore et dolore magna aliqua</p></div>
</section>

<section class="partners">
  <span class="label white">Our partners</span>
  <p class="lead abs center">Sed quia non numquam eius modi tempora incidunt ut labore et dolore magnam aliquam quaerat voluptatem</p>
  <svg class="arrow" style="left:88px;top:224px" width="22" height="42" viewBox="0 0 22 42"><path d="M20 2L2 21l18 19" fill="none" stroke="#fff" stroke-width="2"/></svg>
  <div class="logos">
    <div class="logo-name"><span class="dot"></span>Velmar Corp</div>
    <div class="logo-name">Tarnel Financial</div>
    <div class="logo-name"><span class="dot"></span>Kolvera</div>
    <div class="logo-name">ostrin</div>
    <div class="logo-name"><span class="dot"></span>Brevado</div>
  </div>
  <svg class="arrow" style="left:1087px;top:224px" width="22" height="42" viewBox="0 0 22 42"><path d="M2 2l18 19L2 40" fill="none" stroke="#fff" stroke-width="2"/></svg>
</section>

<section class="conditions">
  <div class="cond-photo" role="img" aria-label="Workshop hall with timber-frame house modules under construction"></div>
  <span class="label yellow">Conditions of our services</span>
  <h2 class="sec-title">Voluptat accusanti dolore</h2>
  <p>But I must explain to you how all this mistaken idea of denouncing pleasure and praising pain was born and I will give you a complete account of the system, and expound the actual teachings of the great explorer of the truth, the master-builder of human happiness. No one rejects, dislikes, or avoids pleasure itself, because it is pleasure, but because those who do not know how to pursue pleasure rationally encounter consequences that are extremely painful.</p>
</section>

<section class="projects">
  <span class="label yellow">Successful projects</span>
  <h2 class="sec-title center">Numquam eius modi tempora incidunt</h2>

  <article class="card" style="left:110px">
    <div class="media" role="img" aria-label="Video still of modern glass building facades" style="background:linear-gradient(160deg,#4a4440,#8a6a55 50%,#3a3634)"><span class="play"><svg width="22" height="26" viewBox="0 0 22 26"><path d="M2 1l19 12L2 25z" fill="#333"/></svg></span></div>
    <h3>Voluptatem Accusantium</h3>
    <p>Sed ut perspiciatis unde omnis iste natus error sit voluptatem accusantium dolore remque laudantium</p>
  </article>
  <article class="card" style="left:445px">
    <div class="media" role="img" aria-label="Video still of metal gears close up" style="background:linear-gradient(160deg,#8a8580,#5a524a 50%,#a09a92)"><span class="play"><svg width="22" height="26" viewBox="0 0 22 26"><path d="M2 1l19 12L2 25z" fill="#333"/></svg></span></div>
    <h3>Perferendis Doloribus</h3>
    <p>Sed ut perspiciatis unde omnis iste natus error sit voluptatem accusantium dolore remque laudantium</p>
  </article>
  <article class="card" style="left:779px">
    <div class="media" role="img" aria-label="Video still of birds flying above a blue fence" style="background:linear-gradient(180deg,#8ea2b8,#3c4c66 60%,#1f2a3c)"><span class="play"><svg width="22" height="26" viewBox="0 0 22 26"><path d="M2 1l19 12L2 25z" fill="#333"/></svg></span></div>
    <h3>Necessitatibus Saepe</h3>
    <p>Sed ut perspiciatis unde omnis iste natus error sit voluptatem accusantium dolore remque laudantium</p>
  </article>
</section>

<section class="team">
  <span class="label yellow">Our team</span>
  <p class="lead abs center">Sed quia consequuntur magni dolores eos qui ratione voluptatem sequi nesciunt.</p>
  <svg class="arrow" style="left:88px;top:287px" width="22" height="42" viewBox="0 0 22 42"><path d="M20 2L2 21l18 19" fill="none" stroke="#bbb" stroke-width="2"/></svg>
  <div class="member" style="left:104px">
    <div class="photo"><div role="img" aria-label="Portrait photo of team member" style="background:linear-gradient(180deg,#6a7f96,#3a4656)"></div></div>
    <h3>Tomáš Hrubec</h3>
    <div class="role">Executive Director</div>
    <div class="contacts"><span>☎ +420 700 100 201</span><span>☎ +420 500 200 302</span><span>✉ hrubec@pramenova-example.eu</span></div>
  </div>
  <div class="member" style="left:573px">
    <div class="photo"><div role="img" aria-label="Portrait photo of team member" style="background:linear-gradient(180deg,#e9e5e2,#b58a74)"></div></div>
    <h3>Mgr.Lenka Dvorská</h3>
    <div class="role">Project Manager</div>
    <div class="contacts"><span>☎ +420 700 100 205</span><span>✉ dvorska@pramenova-example.eu</span></div>
  </div>
  <svg class="arrow" style="left:1087px;top:287px" width="22" height="42" viewBox="0 0 22 42"><path d="M2 2l18 19L2 40" fill="none" stroke="#bbb" stroke-width="2"/></svg>
</section>

<footer class="site-footer">
  <div class="brand"><span class="mark"></span>Pramenova</div>
  <p class="f-about">At vero eos et accusamus et iusto odio dignissimos ducimus qui blanditiis praesentium voluptatum deleniti atque corrupti quos dolores et quas molestias excepturi sint occaecati cupiditate non provident</p>
  <div class="social"><span></span><span></span><span></span><span></span></div>

  <h4 style="left:507px;top:76px">Quick Links</h4>
  <div class="links" style="left:507px;top:118px">Home<br>About us<br>Our Services<br>Partners</div>
  <div class="links" style="left:688px;top:118px">Conditions<br>Projects<br>Team<br>Contact</div>

  <h4 style="left:850px;top:76px">Join Our Newsletter</h4>
  <div class="newsletter"><input type="text" placeholder="Your email"></div>
  <div class="subscribe">SUBSCRIBE</div>

  <p class="copy abs center">Copyrights © 2018, Pramenova. All rights reserved.</p>
</footer>

</body>
</html>
```